Luxury Business Card Design for High-End Window Treatments

Gilded Slatworks
Custom Plantation Shutters & Architectural Shading Systems

⸻

BACK

Daniel Trevick
Owner

Custom Interior & Exterior Window Treatments

919-555-0148
gildedslatworks.com

I have included a picture that I’m hoping we can use on the back, but I’m also wondering if you can get rid of the ladder? Should we get rid of shutters , shades and blinds underneath Gilded Slatworks?

Target Market(s)

High-end residential homeowners, custom home builders, architects, interior designers, and luxury renovation clients seeking premium plantation shutters and motorized architectural shading systems.

Industry/Entity Type

Custom Window treatments

Contact Information for Business Card

Front Gilded Slatworks Custom Plantation Shutters Motorized Architectural Shading Systems BACK Daniel Trevick Owner 919-555-0148 GildedSlatworks.com Custom Interior & Exterior Window Treatments By Appointment

Requirements
Nice to have
• Not 100% sure on nice to halves or the color but you can definitely check out my website to get a better understanding of what I’m trying to do

```html
<!DOCTYPE html>
<html lang="en">
<head>
<meta charset="utf-8">
<title>Gilded Slatworks — Business Card</title>
<link rel="stylesheet" href="https://fonts.googleapis.com/css2?family=Lato:wght@400;700&family=Lora:wght@400;600;700&display=swap">
<style>
  :root {
    --backdrop: #232122;
    --card: #0d0d0d;
    --card-edge: #1a1a1a;
    --gold: #f2c84b;
    --gold-deep: #d9a92c;
    --silver: #e6e6e6;
    --white: #f4f4f4;
  }
  * { margin: 0; padding: 0; box-sizing: border-box; }
  html, body {
    width: 1200px; height: 939px; overflow: hidden;
    background: var(--backdrop);
  }
  .canvas { position: relative; width: 1200px; height: 939px; }

  .card {
    position: absolute;
    width: 700px; height: 400px;
    border-radius: 26px;
    background: linear-gradient(160deg, var(--card-edge), var(--card) 60%);
    box-shadow: -4px 5px 0 var(--gold-deep), -8px 14px 30px rgba(0,0,0,.55);
  }
  .card--front { left: 140px; top: 48px; }
  .card--back  { left: 360px; top: 490px; }

  .brand-name {
    font-family: "Lora", serif;
    font-weight: 400;
    color: var(--silver);
    line-height: 1.05;
  }
  .product-line {
    font-family: "Lora", serif;
    font-weight: 600;
    color: var(--gold);
    display: flex; gap: 22px;
  }
  .tagline {
    position: absolute;
    left: 0; right: 0; bottom: 46px;
    text-align: center;
    font-family: "Lora", serif;
    letter-spacing: .3px;
  }

  /* Front */
  .card--front .lockup {
    position: absolute; left: 0; right: 0; top: 108px;
    display: flex; flex-direction: column; align-items: center;
  }
  .card--front .brand-name { font-size: 52px; text-align: center; }
  .card--front .product-line { font-size: 24px; margin-top: 16px; }
  .card--front .tagline { color: var(--white); font-size: 17px; }

  /* Back */
  .card--back .lockup {
    position: absolute; left: 120px; top: 118px; width: 250px;
    display: flex; flex-direction: column; align-items: center;
  }
  .card--back .brand-name { font-size: 40px; text-align: center; }
  .card--back .product-line { font-size: 18px; margin-top: 12px; gap: 16px; }
  .divider {
    position: absolute; left: 395px; top: 110px;
    width: 1.5px; height: 120px; background: var(--gold-deep);
  }
  .contact { position: absolute; left: 425px; top: 110px; }
  .contact__name {
    font-family: "Lora", serif; font-weight: 700;
    font-size: 27px; color: var(--gold);
  }
  .contact__role {
    font-family: "Lato", sans-serif; font-size: 16px;
    color: var(--white); margin: 4px 0 16px 6px;
  }
  .contact__row {
    display: flex; align-items: center; gap: 10px;
    font-family: "Lato", sans-serif; font-size: 17px;
    color: var(--white); margin: 0 0 8px 12px;
  }
  .contact__row svg { width: 15px; height: 15px; flex: none; }
  .card--back .tagline { color: var(--gold); font-size: 18px; }
</style>
</head>
<body>
<main class="canvas">

  <section class="card card--front" aria-label="Card front">
    <div class="lockup">
      <h1 class="brand-name">Gilded Slatworks</h1>
      <p class="product-line"><span>Shutters</span><span>Shades</span><span>Blinds</span></p>
    </div>
    <p class="tagline">Custom Plantation Shutters &amp; Motorized Architectural Shading Systems</p>
  </section>

  <section class="card card--back" aria-label="Card back">
    <div class="lockup">
      <h2 class="brand-name">Gilded Slatworks</h2>
      <p class="product-line"><span>Shutters</span><span>Shades</span><span>Blinds</span></p>
    </div>
    <div class="divider"></div>
    <div class="contact">
      <p class="contact__name">Daniel Trevick</p>
      <p class="contact__role">Owner</p>
      <p class="contact__row">
        <svg viewBox="0 0 24 24" aria-hidden="true"><path fill="var(--gold)" d="M6.6 10.8a15.1 15.1 0 0 0 6.6 6.6l2.2-2.2a1 1 0 0 1 1-.25 11.4 11.4 0 0 0 3.6.57 1 1 0 0 1 1 1V20a1 1 0 0 1-1 1A17 17 0 0 1 3 4a1 1 0 0 1 1-1h3.5a1 1 0 0 1 1 1c0 1.25.2 2.45.57 3.57a1 1 0 0 1-.25 1z"/></svg>
        919-555-0148
      </p>
      <p class="contact__row">
        <svg viewBox="0 0 24 24" aria-hidden="true"><circle cx="12" cy="12" r="10" fill="var(--gold)"/><path d="M2 12h20M12 2c3 3 3 17 0 20M12 2c-3 3-3 17 0 20" stroke="var(--card)" stroke-width="1.6" fill="none"/></svg>
        gildedslatworks.com
      </p>
    </div>
    <p class="tagline">Custom Interior &amp; Exterior Window Treatments</p>
  </section>

</main>
</body>
</html>
```